Corporate Design für Gebäudereinigung
Zielgruppe
Das Unternehmen ist in der Reinigungsbranche tätig. Es werden alle möglichen Reinigungstätigkeiten durchgeführt.
Von klassischer Unterhaltsreinigung in Stiegenhäusern oder Büros bis hin zu Spezialreinigungen wie Fassaden, Dächer, Denkmäler oder unterschiedlichsten Böden.
Zielgruppe kann kaum definiert werden, da Private wie auch Firmenkunden angesprochen werden sollen.
From classic maintenance cleaning in stairwells or offices to special cleaning such as facades, roofs, monuments or a wide variety of floors.
Target group can hardly be defined, since private as well as corporate customers should be addressed.
Aufgabenstellung
Wichtig ist, dass nicht zu viele Farben verwendet werden.
Design eher hell sprich 'sauber' nicht dunkel und schwerfällig.
Vielen Dank!
It is important not to use too many colors.
Design rather light, i.e. 'clean' not dark and impurely.
Thank you!

```html
<!DOCTYPE html>
<html lang="de">
<head>
<meta charset="utf-8">
<title>Klarhaus Gebäudereinigung – Geschäftsausstattung</title>
<link rel="stylesheet" href="https://fonts.googleapis.com/css2?family=Cinzel:wght@400&family=Open+Sans:wght@400;600&display=swap">
<style>
  :root{
    --navy:#0f1f3a;
    --blue:#2e9bd6;
    --orange:#e8732a;
    --paper:#ffffff;
    --panel:#e6e6e6;
    --canvas:#ffffff;
    --ink:#4a4f58;
    --grey:#c9c9c9;
  }
  *{box-sizing:border-box;margin:0;padding:0}
  html,body{width:1200px;height:1200px;overflow:hidden;background:var(--canvas)}
  body{position:relative;font-family:"Open Sans",Arial,sans-serif;color:var(--ink)}
  .board{position:absolute;left:330px;top:10px;width:540px;height:1180px;background:var(--panel)}
  .piece{position:absolute;box-shadow:0 3px 8px rgba(0,0,0,.25);overflow:hidden}
  .paper{background:var(--paper)}
  .dark{background:var(--navy)}

  /* wordmark */
  .mark{position:absolute;display:flex;flex-direction:column;align-items:center;
        font-family:"Cinzel",Georgia,serif;font-weight:400;color:var(--blue);line-height:1.1;text-align:center}
  .mark .dot{border-radius:50%;border:1.5px solid currentColor;margin-bottom:3px}
  .mark .name{display:flex;align-items:center;gap:4px;letter-spacing:.04em}
  .mark .name::before,.mark .name::after{content:"";height:1px;background:currentColor}
  .mark .sub{letter-spacing:.02em}
  .mark.xs .dot{width:9px;height:9px}
  .mark.xs .name{font-size:5px}.mark.xs .name::before,.mark.xs .name::after{width:8px}
  .mark.xs .sub{font-size:3.6px}
  .mark.sm .dot{width:14px;height:14px}
  .mark.sm .name{font-size:8px}.mark.sm .name::before,.mark.sm .name::after{width:12px}
  .mark.sm .sub{font-size:5px}
  .mark.md .dot{width:18px;height:18px}
  .mark.md .name{font-size:10px}.mark.md .name::before,.mark.md .name::after{width:16px}
  .mark.md .sub{font-size:6px}
  .mark.lg .dot{width:34px;height:34px;border-width:2px;margin-bottom:6px}
  .mark.lg .name{font-size:15px;gap:6px}.mark.lg .name::before,.mark.lg .name::after{width:28px}
  .mark.lg .sub{font-size:9px}

  .tiny{font-size:3.4px;line-height:1.5;color:var(--ink)}
  .contact-row{display:flex;align-items:center;gap:2px}
  .contact-row i{display:inline-block;width:3px;height:3px;background:var(--blue)}
  .card-label{position:absolute;font-size:14px;color:#222;font-family:"Open Sans",Arial,sans-serif}

  /* envelope flap */
  .flap{position:absolute;left:0;top:0;width:100%;height:26px}
  .window{position:absolute;right:12px;top:58px;width:58px;height:28px;background:var(--grey);border-radius:4px}

  /* letterhead */
  .body-text{position:absolute;left:22px;right:22px;top:84px;font-size:4px;line-height:1.45;color:#666}
  .body-text p{margin-bottom:5px}
  .foot{position:absolute;left:22px;right:22px;bottom:12px;display:flex;justify-content:space-between}

  .photo{position:absolute;background:linear-gradient(160deg,#dfe8ef 0%,#b9c9d6 55%,#8ea3b4 100%)}
</style>
</head>
<body>
<main class="board">

  <!-- envelope back -->
  <section class="piece paper" style="left:48px;top:74px;width:198px;height:102px">
    <svg class="flap" viewBox="0 0 198 26" preserveAspectRatio="none" aria-hidden="true">
      <polygon points="0,0 198,0 194,26 4,26" fill="#0f1f3a"/>
    </svg>
    <div class="mark xs" style="left:0;right:0;top:4px">
      <span class="dot"></span><span class="name">Klarhaus</span><span class="sub">Gebäudereinigung E.U.</span>
    </div>
  </section>

  <!-- dark presentation card -->
  <section class="piece dark" style="left:298px;top:44px;width:198px;height:124px">
    <div class="mark md" style="left:0;right:0;top:38px">
      <span class="dot"></span><span class="name">Klarhaus</span><span class="sub">Gebäudereinigung E.U.</span>
    </div>
  </section>

  <!-- envelope front -->
  <section class="piece paper" style="left:48px;top:204px;width:198px;height:102px">
    <div class="mark sm" style="left:8px;width:66px;top:16px">
      <span class="dot"></span><span class="name">Klarhaus</span><span class="sub">Gebäudereinigung E.U.</span>
    </div>
    <div class="tiny" style="position:absolute;left:12px;top:60px">
      <div>Lindengasse 12, 1070 Wien</div>
      <div class="contact-row"><i></i>+43 1 234 5678</div>
      <div class="contact-row"><i></i>+43 1 234 5679</div>
      <div class="contact-row"><i></i>+43 660 123 456</div>
      <div class="contact-row"><i></i>office@klarhaus-reinigung.at</div>
      <div class="contact-row"><i></i>www.klarhaus-reinigung.at</div>
    </div>
    <div class="window"></div>
  </section>

  <!-- business cards A -->
  <span class="card-label" style="left:276px;top:208px">A</span>
  <section class="piece paper" style="left:296px;top:192px;width:92px;height:54px">
    <div class="tiny" style="position:absolute;left:7px;top:8px;font-size:3.8px">Anna Berger<br>Geschäftsführung</div>
    <div class="mark xs" style="right:6px;top:5px">
      <span class="dot"></span><span class="name">Klarhaus</span><span class="sub">Gebäudereinigung E.U.</span>
    </div>
    <div class="tiny" style="position:absolute;left:7px;top:30px">
      <div class="contact-row"><i></i>+43 1 234 5678</div>
      <div class="contact-row"><i></i>office@klarhaus.at</div>
      <div class="contact-row"><i></i>klarhaus-reinigung.at</div>
    </div>
    <div class="tiny" style="position:absolute;left:50px;top:30px">
      <div class="contact-row"><i></i>Lindengasse 12</div>
      <div class="contact-row"><i></i>1070 Wien</div>
    </div>
  </section>
  <section class="piece dark" style="left:404px;top:192px;width:92px;height:54px">
    <div class="mark xs" style="left:0;right:0;top:14px">
      <span class="dot"></span><span class="name">Klarhaus</span><span class="sub">Gebäudereinigung E.U.</span>
    </div>
  </section>

  <!-- business cards B -->
  <span class="card-label" style="left:276px;top:284px">B</span>
  <section class="piece paper" style="left:296px;top:266px;width:92px;height:54px">
    <div class="mark xs" style="left:4px;width:44px;top:16px">
      <span class="dot"></span><span class="name">Klarhaus</span><span class="sub">Gebäudereinigung E.U.</span>
    </div>
    <div class="tiny" style="position:absolute;left:52px;top:8px">
      <div style="font-size:3.8px">Anna Berger</div>
      <div>Geschäftsführung</div>
      <div class="contact-row" style="margin-top:4px"><i></i>+43 1 234 5678</div>
      <div class="contact-row"><i></i>office@klarhaus.at</div>
      <div class="contact-row"><i></i>Lindengasse 12</div>
      <div class="contact-row"><i></i>1070 Wien</div>
    </div>
  </section>
  <section class="piece dark" style="left:404px;top:266px;width:92px;height:54px">
    <div class="mark xs" style="left:0;right:0;top:14px">
      <span class="dot"></span><span class="name">Klarhaus</span><span class="sub">Gebäudereinigung E.U.</span>
    </div>
  </section>

  <!-- folder -->
  <section class="piece dark" style="left:44px;top:352px;width:210px;height:286px">
    <div class="mark lg" style="left:0;right:0;top:114px">
      <span class="dot"></span><span class="name">Klarhaus</span><span class="sub">Gebäudereinigung E.U.</span>
    </div>
  </section>

  <!-- letterhead -->
  <section class="piece paper" style="left:290px;top:352px;width:210px;height:286px">
    <div class="mark sm" style="left:0;right:0;top:22px">
      <span class="dot"></span><span class="name">Klarhaus</span><span class="sub">Gebäudereinigung E.U.</span>
    </div>
    <div class="body-text">
      <p>Sehr geehrte Damen und Herren, vielen Dank für Ihre Anfrage. Gerne übernehmen wir die regelmäßige Reinigung Ihrer Büros, Stiegenhäuser und Gemeinschaftsflächen mit geschultem Personal und umweltschonenden Mitteln.</p>
      <p>Auch Spezialreinigungen von Fassaden, Dächern, Denkmälern und Böden aller Art führen wir zuverlässig und termingerecht durch.</p>
      <p>Unser Angebot erstellen wir nach einer kostenlosen Besichtigung vor Ort. Wir freuen uns auf Ihre Rückmeldung.</p>
      <p>Mit freundlichen Grüßen<br>Anna Berger</p>
    </div>
    <div class="tiny" style="position:absolute;left:22px;bottom:30px">Lindengasse 12, 1070 Wien</div>
    <div class="foot tiny">
      <div><div class="contact-row"><i></i>+43 1 234 5678</div><div class="contact-row"><i></i>+43 1 234 5679</div></div>
      <div class="contact-row"><i></i>+43 660 123 456</div>
      <div><div class="contact-row"><i></i>office@klarhaus-reinigung.at</div><div class="contact-row"><i></i>www.klarhaus-reinigung.at</div></div>
    </div>
  </section>

  <!-- stamp imprint, flat -->
  <section class="piece paper" style="left:44px;top:672px;width:220px;height:152px">
    <div class="mark md" style="left:0;right:0;top:52px;color:#8a8f96">
      <span class="dot"></span><span class="name">Klarhaus</span><span class="sub">Gebäudereinigung E.U.</span>
    </div>
  </section>

  <!-- business card front and back, flat -->
  <section class="piece dark" style="left:276px;top:672px;width:224px;height:152px">
    <div class="mark sm" style="left:0;right:0;top:54px">
      <span class="dot"></span><span class="name">Klarhaus</span><span class="sub">Gebäudereinigung E.U.</span>
    </div>
  </section>

  <!-- poster -->
  <section class="piece paper" style="left:150px;top:852px;width:240px;height:300px;border:4px solid #7f9fd6">
    <div class="photo" role="img" aria-label="Foto eines hellen, modernen Bürogebäudes" style="left:0;top:0;right:0;bottom:0"></div>
    <div class="mark md" style="left:0;right:0;top:120px;color:var(--navy)">
      <span class="dot"></span><span class="name">Klarhaus</span><span class="sub">Gebäudereinigung E.U.</span>
    </div>
  </section>

</main>
</body>
</html>
```